Health Promotion Charity Info-graphic of 2013 Activities

We need an Info-graphic which will be printed on A4 for distribution to our members, government, key stakeholders and grant providers. It will also be uploaded to our website - www.bright-sprouts.com.au

PROJECT BRIEF – Branding as per Bright Sprouts Association
The aim of this infographic is to show the work that Bright Sprouts Association did in 2013. It will be a pictorial annual report. It is to communicate to a wide audience the size and reach of Bright Sprouts Association activities.
We are a health promotion charity that supports schools to deliver healthy food services and our aim is to improve food literacy so kids know what to eat, when.... Our aim is to reduce diet related disease - mainly those relating to overweight and obesity. The infographic should be in keeping with our brand - see www.bright-sprouts.com.au

Using the following information
Our Members
In 2013 we had a total membership of 1,200
Our members are 1,137 Schools
20 Affiliates
24 Individuals
19 Leasees who operate 45 school canteens.
Our school members are
Public Sector Schools 846
Independent Schools 78
Catholic Schools 204
High schools 196
Primary 845
Central schools 30

There are 3082 schools in NSW – so we have 38% as members.

Our services
Supporting Schools
We answered 1078 enquiries through our telephone and email service.
We under took 20 menu assessments
22 school canteens had a business diagnostic
We flew to the regions and attended network meetings and school visits throughout New South Wales: South coast, Central Coast, north coast, illawarra, hunter new England and Dubbo

Publications
We produced the summer and winter editions of Bright Sprouts Tuckshop Corner magazine and
the Annual Bright Sprouts Tuckshop Corner Buyers Guide.

Food Industry
We work with the food industry to change the nutritional value of food
There were 57 food companies that registered 823 food products suitable for school canteens. Of these products, 359 were Green products and 464 amber products.

Community Activities
We worked with Riverbend and Kestrel Hills councils delivering 8 school holiday cooking classes to 80 children and their parents.

WEBSITE STATS – www.bright-sprouts.com.au
200,381 web visits
157,601 unique visitors
491.495 page views
2.45 pages per visitor

We worked with VOLMO to develop the Crunch Club initiative which resulted in 79,289 Orbit OS and Lumen Downloads and
10,629 subscribers to the weekly VOLMO email Crunch Club menu and shopping list.

Our funding
Total Income - $1,371,438
Government - $747,870 (54%)
Membership - $83,228 (6%)
Fee for Service – $42,946 (4%)
Other - $497,395(36%)
Total Equity $50,811

0555a3
9bcb3c
0593ce

```html
<!DOCTYPE html>
<html lang="en">
<head>
<meta charset="utf-8">
<title>Bright Sprouts Association – 2013 Activities</title>
<link rel="stylesheet" href="https://fonts.googleapis.com/css2?family=Montserrat:wght@700;800&family=Open+Sans:wght@300;400;700&family=Noto+Serif:wght@400;700&display=swap">
<style>
  :root {
    --navy: #0555a3;
    --sky: #0593ce;
    --lime: #9bcb3c;
    --white: #ffffff;
    --rule: #e3e3e3;
  }
  * { margin: 0; padding: 0; box-sizing: border-box; }
  html, body { width: 849px; height: 1200px; overflow: hidden; background: var(--white); }
  .sheet { position: relative; width: 849px; height: 1200px; overflow: hidden; background: var(--white); }
  .abs { position: absolute; }
  .heading { font-family: "Montserrat", sans-serif; font-weight: 800; text-transform: uppercase; letter-spacing: 0.5px; }
  .light { font-family: "Open Sans", sans-serif; font-weight: 300; }
  .light b { font-weight: 700; }
  .serif { font-family: "Noto Serif", serif; }
  .num { font-family: "Montserrat", sans-serif; font-weight: 800; }

  /* brand */
  .brand { left: 48px; top: 90px; display: flex; align-items: center; gap: 12px; }
  .brand-dot { width: 52px; height: 52px; border-radius: 50%; background: var(--lime); }
  .brand-name { font-family: "Montserrat", sans-serif; font-weight: 800; font-size: 27px; color: var(--sky); line-height: 1.05; }
  .brand-rule { left: 286px; top: 18px; width: 1px; height: 214px; background: var(--rule); }

  /* services */
  .services-bg { left: 455px; top: 0; width: 460px; height: 250px; background: var(--navy); border-radius: 125px 0 0 125px; }
  .services { left: 537px; top: 31px; width: 300px; color: var(--white); }
  .services h2 { font-size: 27px; line-height: 30px; }
  .services p { font-size: 15px; line-height: 17.3px; }

  /* members */
  .members { left: 47px; top: 279px; width: 390px; color: var(--navy); }
  .members h2 { font-size: 32px; line-height: 34px; }
  .members p { font-size: 15px; line-height: 17px; }
  .members p + p { margin-top: 17px; }

  /* panels */
  .panel { color: var(--white); padding: 13px 32px 0 33px; }
  .panel h2 { font-size: 27px; line-height: 30px; }
  .panel p { font-size: 15px; line-height: 17px; }
  .publications { left: 451px; top: 285px; width: 398px; height: 127px; background: var(--sky); }
  .food { left: 451px; top: 448px; width: 398px; height: 182px; background: var(--lime); }

  /* community */
  .community { left: 0; top: 663px; width: 849px; height: 134px; background: var(--sky); color: var(--white); }
  .community svg { position: absolute; left: 106px; top: 20px; }
  .community .copy { position: absolute; left: 242px; top: 22px; }
  .community h2 { font-size: 27px; line-height: 34px; }
  .community p { font-size: 17px; line-height: 24px; }

  /* website */
  .web-band { left: 330px; top: 833px; width: 519px; height: 165px; background: var(--lime); }
  .web-ring { left: 280px; top: 811px; width: 166px; height: 166px; border-radius: 50%; background: var(--lime); }
  .web-ring svg { position: absolute; left: 0; top: 0; }
  .web { left: 450px; top: 843px; color: var(--white); }
  .web h2 { font-size: 27px; line-height: 30px; }
  .web .url { font-family: "Noto Serif", serif; font-size: 14px; line-height: 16px; }
  .stats { margin-top: 11px; display: grid; grid-template-columns: 164px 180px; row-gap: 11px; }
  .stat { display: flex; gap: 9px; align-items: flex-start; }
  .stat-ico { flex: none; width: 28px; height: 28px; border-radius: 50%; background: var(--white); margin-top: 4px; display: flex; align-items: center; justify-content: center; }
  .stat-txt { font-family: "Noto Serif", serif; font-size: 16px; line-height: 17px; }
  .stat-txt strong { font-family: "Montserrat", sans-serif; font-weight: 800; font-size: 15px; display: block; }

  /* partner */
  .partner-bg { left: -90px; top: 820px; width: 500px; height: 500px; border-radius: 50%; background: var(--navy); }
  .partner-ico { left: 46px; top: 878px; }
  .partner { left: 47px; top: 990px; width: 235px; color: var(--white); font-size: 16px; line-height: 24.3px; }

  /* funding */
  .funding-band { left: 490px; top: 1033px; width: 359px; height: 167px; background: var(--sky); }
  .funding-badge { left: 318px; top: 1008px; width: 204px; height: 204px; border-radius: 50%; background: var(--sky); border: 5px solid var(--white); color: var(--white); text-align: center; }
  .funding-badge .sign { font-family: "Open Sans", sans-serif; font-weight: 400; font-size: 84px; line-height: 86px; margin-top: 8px; }
  .funding-badge .label { font-size: 24px; line-height: 31px; }
  .funding { left: 560px; top: 1053px; color: var(--white); font-family: "Noto Serif", serif; font-size: 15px; line-height: 20.6px; }
  .funding .num { font-size: 15px; margin-right: 4px; }
</style>
</head>
<body>
<main class="sheet">

  <div class="abs brand">
    <span class="brand-dot"></span>
    <span class="brand-name">Bright<br>Sprouts</span>
  </div>
  <div class="abs brand-rule"></div>

  <div class="abs services-bg"></div>
  <section class="abs services">
    <h2 class="heading">Our Services</h2>
    <p class="light">Supporting Schools<br>We answered <b>1078</b> enquiries<br>through our telephone and email<br>service. We under took <b>20</b> menu<br>assessments <b>22</b> school canteens<br>had a business diagnostic. We<br>flew to the regions and attended<br>network meetings and school<br>visits throughout New South Wales</p>
  </section>

  <section class="abs members">
    <h2 class="heading">Our Members</h2>
    <p class="serif">In 2013 we had a total membership of 1,200<br><span class="num">1,137</span> Schools Members<br><span class="num">20</span> Affiliates<br><span class="num">24</span> Individuals<br><span class="num">19</span> Leasees who operate 45 school canteens.</p>
    <p class="serif">Our school members are<br><span class="num">846</span> Public Sector Schools<br><span class="num">78</span> Independent Schools<br><span class="num">204</span> Catholic Schools<br><span class="num">196</span> High schools<br><span class="num">845</span> Primary<br><span class="num">30</span> Central schools</p>
    <p class="serif">There are 3082 schools in NSW –<br>so we have 38% as members.</p>
  </section>

  <section class="abs panel publications">
    <h2 class="heading">Publications</h2>
    <p class="light">We produced the summer and winter<br>editions of Bright Sprouts Tuckshop Corner<br>magazine and the Annual Bright Sprouts<br>Tuckshop Corner Buyers Guide.</p>
  </section>

  <section class="abs panel food">
    <h2 class="heading">Food Industry</h2>
    <p class="light">We work with the food industry to change<br>the nutritional value of food<br>There were <b>57</b> food companies that<br>registered <b>823</b> food products suitable for<br>school canteens. Of these products,<br><b>359</b> were Green products and <b>464</b> amber<br>products.</p>
  </section>

  <section class="abs community">
    <svg width="106" height="96" viewBox="0 0 106 96" aria-hidden="true">
      <polyline points="15,83 42,41 70,68 92,8" fill="none" stroke="#fff" stroke-width="6"/>
      <circle cx="15" cy="83" r="10" fill="#0593ce" stroke="#fff" stroke-width="5"/>
      <circle cx="42" cy="41" r="10" fill="#0593ce" stroke="#fff" stroke-width="5"/>
      <circle cx="70" cy="68" r="10" fill="#0593ce" stroke="#fff" stroke-width="5"/>
      <circle cx="92" cy="12" r="10" fill="#0593ce" stroke="#fff" stroke-width="5"/>
    </svg>
    <div class="copy">
      <h2 class="heading">Community Activities</h2>
      <p class="light">We worked with Riverbend and Kestrel Hills councils delivering<br><b>8</b> school holiday cooking classes to <b>80</b> children and their parents.</p>
    </div>
  </section>

  <div class="abs partner-bg"></div>
  <svg class="abs partner-ico" width="92" height="92" viewBox="0 0 92 92" aria-hidden="true">
    <g fill="#fff">
      <path d="M20 6 a16 16 0 0 0 -12 26 l50 50 a6 6 0 0 0 9 -9 l-50 -50 a16 16 0 0 0 -6 -16 l0 12 -8 4 -6 -6 z"/>
      <rect x="58" y="4" width="14" height="30" rx="3" transform="rotate(45 65 19)"/>
      <rect x="34" y="30" width="7" height="56" transform="rotate(45 37 58)"/>
    </g>
  </svg>
  <p class="abs partner light">We worked with VOLMO to develop the Crunch Club initiative which resulted in <b>79,289</b> Orbit OS and Lumen Downloads and <b>10,629</b> subscribers to the weekly VOLMO email Crunch Club menu and shopping list.</p>

  <div class="abs web-band"></div>
  <div class="abs web-ring">
    <svg width="166" height="166" viewBox="0 0 166 166" aria-hidden="true">
      <circle cx="83" cy="83" r="66" fill="none" stroke="#fff" stroke-width="2" stroke-dasharray="3 3"/>
      <g fill="none" stroke="#fff" stroke-width="5">
        <circle cx="83" cy="83" r="30"/>
        <ellipse cx="83" cy="83" rx="13" ry="30"/>
        <line x1="53" y1="83" x2="113" y2="83"/>
        <path d="M58 68 h50 M58 98 h50"/>
      </g>
    </svg>
  </div>
  <section class="abs web">
    <h2 class="heading">Website Stats</h2>
    <div class="url">www.bright-sprouts.com.au</div>
    <div class="stats">
      <div class="stat"><span class="stat-ico"><svg width="14" height="14" viewBox="0 0 14 14"><circle cx="7" cy="7" r="6" fill="#9bcb3c"/></svg></span><div class="stat-txt"><strong>200,381</strong>web visits</div></div>
      <div class="stat"><span class="stat-ico"><svg width="14" height="14" viewBox="0 0 14 14"><polyline points="2,7 6,11 12,3" fill="none" stroke="#9bcb3c" stroke-width="2.5"/></svg></span><div class="stat-txt"><strong>491.495</strong>page views</div></div>
      <div class="stat"><span class="stat-ico"><svg width="14" height="14" viewBox="0 0 14 14"><circle cx="7" cy="4" r="3" fill="#9bcb3c"/><path d="M2 13 a5 5 0 0 1 10 0 z" fill="#9bcb3c"/></svg></span><div class="stat-txt"><strong>157,601</strong>unique visitors</div></div>
      <div class="stat"><span class="stat-ico"><svg width="14" height="14" viewBox="0 0 14 14"><circle cx="6" cy="6" r="4" fill="none" stroke="#9bcb3c" stroke-width="2"/><line x1="9" y1="9" x2="13" y2="13" stroke="#9bcb3c" stroke-width="2.5"/></svg></span><div class="stat-txt"><strong>2.45</strong>pages per visitor</div></div>
    </div>
  </section>

  <div class="abs funding-band"></div>
  <div class="abs funding-badge">
    <div class="sign">$</div>
    <div class="label heading">Our<br>Funding</div>
  </div>
  <p class="abs funding"><span class="num">$1,371,438</span> Total Income<br><span class="num">$747,870 (54%)</span> Government<br><span class="num">$83,228 (6%)</span> Membership<br><span class="num">$42,946 (4%)</span> Fee for Service<br><span class="num">$497,395(36%)</span> Other<br><span class="num">$50,811</span> Total Equity</p>

</main>
</body>
</html>
```